Website Design for The Elder Nook

Please design and code a new website.
Here are the sites I like best:
http://www.voyaglint.com/alternate/
http://www.wheelgiftbay.org
Please make it similar but look at the competitor site (below) for images and wording. This is NOT a car donation site. It's a senior lead placement site like https://www.kinhavenfinder.com. I just like this sites above as a lead generation sites.
Competitor site:
https://www.kinhavenfinder.com (use ideas / verbiage from this site)
Updates
Competitor site:
Coding
Coded - Design and coding required
Number of Pages Required
1 page
Look and feel
Each slider illustrates characteristics of the customer's brand and the style your logo design should communicate.

```html
<!DOCTYPE html>
<html lang="en">
<head>
<meta charset="utf-8">
<title>The Elder Nook — Senior Living Advisors</title>
<link href="https://fonts.googleapis.com/css2?family=Crimson+Pro:wght@400;500&family=Lato:wght@300;400;700&display=swap" rel="stylesheet">
<style>
:root{
  --blue:#0e5aa7;
  --blue-dark:#0a4b8f;
  --green:#8cc63f;
  --text:#333;
  --muted:#666;
  --line:#e2e2e2;
  --white:#fff;
}
*{box-sizing:border-box;margin:0;padding:0}
html,body{width:1200px;height:3040px;overflow:hidden}
body{position:relative;font-family:'Lato',sans-serif;color:var(--text);background:var(--white)}
.serif{font-family:'Crimson Pro',serif}
.abs{position:absolute}

/* header */
.site-header{position:absolute;top:0;left:0;width:1200px;height:91px}
.brand{position:absolute;left:142px;top:30px;display:flex;align-items:center;gap:10px;font-family:'Crimson Pro',serif;font-size:27px;color:var(--blue)}
.brand-dot{width:22px;height:22px;border-radius:50%;background:var(--green)}
.call{position:absolute;left:572px;top:22px;display:flex;align-items:center;gap:12px}
.call-label{font-family:'Crimson Pro',serif;font-size:13px;color:#444}
.call-number{font-size:24px;color:#222;letter-spacing:.3px}
.badge{position:absolute;left:806px;top:22px;width:126px;height:48px;background:var(--blue);border-radius:4px}
.lang{position:absolute;left:957px;top:29px;width:102px;height:33px;border:1px solid var(--line);display:flex;align-items:center;justify-content:center;gap:6px;font-size:13px;color:#555}
.lang-chip{width:34px;height:17px;background:var(--blue)}

.main-nav{position:absolute;top:91px;left:0;width:1200px;height:42px;background:var(--blue)}
.main-nav ul{list-style:none;position:absolute;left:142px;top:0;display:flex;height:42px}
.main-nav li{font-family:'Crimson Pro',serif;font-size:14px;color:var(--white);padding:0 11px;line-height:42px;border-right:1px solid rgba(255,255,255,.2);letter-spacing:.2px}
.main-nav li.active{background:var(--blue-dark);border-bottom:3px solid var(--green)}

/* hero */
.hero{position:absolute;top:133px;left:0;width:1200px;height:573px;background:linear-gradient(100deg,#6d7a8c 0%,#a6a9b0 30%,#c8bcb2 50%,#d6d2cc 70%,#e4e6e3 100%)}
.hero-caption{position:absolute;left:0;width:1200px;top:510px;text-align:center;font-family:'Crimson Pro',serif;font-size:36px;color:var(--white);text-shadow:0 2px 4px rgba(0,0,0,.5)}
.hero-caption em{font-style:italic}
.inquiry{position:absolute;left:694px;top:46px;width:365px;height:417px;background:rgba(240,240,240,.88)}
.inquiry h2{height:63px;background:var(--green);color:var(--white);font-family:'Crimson Pro',serif;font-weight:400;font-size:28px;text-align:center;line-height:63px}
.field{position:absolute;left:29px;width:306px;height:42px;background:var(--white);border:1px solid #ddd;display:flex;font-size:13px;color:#666}
.field .ico{width:40px;border-right:1px solid #ddd;display:flex;align-items:center;justify-content:center;background:#f7f7f7}
.field span.ph{padding-left:16px;line-height:40px}
.submit{position:absolute;left:29px;top:342px;width:306px;height:38px;background:var(--blue);color:var(--white);font-family:'Crimson Pro',serif;font-size:17px;text-align:center;line-height:38px}

/* support */
.section-title{position:absolute;left:0;width:1200px;text-align:center;font-family:'Crimson Pro',serif;font-weight:400;font-size:32px;color:var(--blue)}
.lead{position:absolute;left:200px;width:800px;text-align:center;font-size:14.5px;line-height:24px;color:#333}
.feature{position:absolute;top:899px;width:171px;height:181px;border:1px solid var(--line);box-shadow:0 2px 6px rgba(0,0,0,.08);text-align:center}
.feature svg{margin-top:24px}
.feature p{font-size:18px;line-height:21px;color:#333;margin-top:8px;font-weight:300}
.nocost{position:absolute;top:1132px;left:142px;font-family:'Crimson Pro',serif;font-size:27px;color:var(--blue)}
.nocost b{color:var(--green);font-weight:400}
.nocost-text{position:absolute;top:1126px;left:426px;font-size:17px;line-height:24px;color:#333;font-weight:300}
.nocost-call{position:absolute;top:1135px;left:869px;font-size:21px;color:var(--blue);font-weight:300}

/* advisor band */
.advisor{position:absolute;top:1251px;left:0;width:1200px;height:480px;background:linear-gradient(90deg,#1c5fad,#1a63b4 50%,#1b5fae)}
.advisor-people{position:absolute;inset:0;background:linear-gradient(180deg,rgba(20,70,140,.0),rgba(10,50,110,.25))}
.advisor h2{position:absolute;top:74px;left:0;width:1200px;text-align:center;font-family:'Crimson Pro',serif;font-weight:400;font-size:32px;color:var(--white)}
.advisor .sub{position:absolute;top:126px;left:0;width:1200px;text-align:center;font-size:14.5px;color:var(--white)}
.perk{position:absolute;top:173px;width:200px;text-align:center;color:var(--white)}
.perk .ring{width:98px;height:98px;border:1.5px solid var(--white);border-radius:50%;margin:0 auto;display:flex;align-items:center;justify-content:center}
.perk p{margin-top:12px;font-size:15.5px;line-height:20px;font-weight:300}
.search{position:absolute;top:350px;left:299px;width:603px;height:44px;background:var(--white);border-radius:2px}
.search .ph{position:absolute;left:20px;top:13px;font-size:14.5px;color:#333}
.search .go{position:absolute;right:4px;top:4px;width:222px;height:36px;background:var(--green);color:var(--white);font-family:'Crimson Pro',serif;font-size:17px;text-align:center;line-height:36px}

/* testimonials */
.quote{position:absolute;top:1870px;width:284px;height:148px;border:1px solid var(--line);padding:16px 17px;font-size:13px;line-height:21.5px;color:#777;letter-spacing:.2px}
.quote .mark{position:absolute;right:20px;bottom:6px;font-family:'Crimson Pro',serif;font-size:90px;line-height:60px;color:#eee}
.author{position:absolute;top:1995px;display:flex;align-items:center;gap:20px}
.avatar{width:70px;height:70px;border-radius:50%;border:3px solid var(--blue);background:#e8e2dc}
.author span{font-family:'Crimson Pro',serif;font-size:16px;color:#333;margin-top:-2px}
.btn-green{position:absolute;background:var(--green);color:var(--white);font-family:'Crimson Pro',serif;font-size:17px;text-align:center}

/* veteran band */
.veteran{position:absolute;top:2215px;left:0;width:1200px;height:290px;background:linear-gradient(120deg,#1b2640 0%,#3a2a34 40%,#5a1a22 70%,#3b1218 100%)}
.veteran h2{position:absolute;top:68px;width:1200px;text-align:center;font-family:'Crimson Pro',serif;font-weight:400;font-size:28px;color:var(--white)}
.veteran p{position:absolute;top:112px;width:1200px;text-align:center;font-size:14.5px;line-height:24px;color:var(--white);font-weight:300}

/* states */
.states{position:absolute;top:2639px;left:0;width:1200px}
.states ul{position:absolute;list-style:none;font-size:13px;line-height:21.8px;color:#444}
.states li::before{content:"› ";color:#444}

/* footer */
.site-footer{position:absolute;top:2871px;left:0;width:1200px;height:169px;background:var(--blue)}
.foot-nav{position:absolute;top:50px;left:172px;display:flex;gap:33px;list-style:none;font-family:'Crimson Pro',serif;font-size:12px;color:var(--white);letter-spacing:.2px}
.foot-rule{position:absolute;top:111px;left:142px;width:917px;height:1px;background:rgba(255,255,255,.25)}
.copyright{position:absolute;top:131px;left:142px;font-size:13px;color:var(--white)}
.social{position:absolute;top:126px;left:945px;display:flex;gap:6px}
.social i{width:24px;height:24px;border-radius:50%;border:1.5px solid var(--white);display:block;background:rgba(255,255,255,.12)}
</style>
</head>
<body>

<header class="site-header">
  <div class="brand"><span class="brand-dot"></span>The Elder Nook</div>
  <div class="call">
    <svg width="34" height="34" viewBox="0 0 24 24" fill="none" stroke="#0e5aa7" stroke-width="1.4"><path d="M5 3h4l2 5-2.5 1.5a11 11 0 0 0 6 6L16 13l5 2v4a2 2 0 0 1-2 2A17 17 0 0 1 3 5a2 2 0 0 1 2-2z"/></svg>
    <div><div class="call-label">Talk to a local advisor for FREE</div><div class="call-number">(123) 456-7890</div></div>
  </div>
  <div class="badge" role="img" aria-label="Accreditation badge"></div>
  <div class="lang">EN : <span class="lang-chip"></span>
    <svg width="9" height="6" viewBox="0 0 9 6"><path d="M1 1l3.5 3.5L8 1" stroke="#555" fill="none"/></svg></div>
</header>

<nav class="main-nav">
  <ul>
    <li class="active">ASSISTED LIVING</li>
    <li>MEMORY CARE</li>
    <li>NURSING HOMES</li>
    <li>MORE LIVING OPTIONS ⌄</li>
    <li>PLANNING &amp; ADVICE</li>
    <li>HOW OUR SERVICE WORKS</li>
  </ul>
</nav>

<section class="hero" role="img" aria-label="Photo of a smiling young woman holding hands with an elderly woman">
  <form class="inquiry">
    <h2>Quick Inquiry</h2>
    <div class="field" style="top:92px"><div class="ico"><svg width="12" height="12" viewBox="0 0 12 12" fill="#555"><circle cx="6" cy="3.5" r="2.8"/><path d="M1 12a5 5 0 0 1 10 0z"/></svg></div><span class="ph">Name</span></div>
    <div class="field" style="top:145px"><div class="ico"><svg width="12" height="12" viewBox="0 0 24 24" fill="#555"><path d="M5 3h4l2 5-2.5 1.5a11 11 0 0 0 6 6L16 13l5 2v4a2 2 0 0 1-2 2A17 17 0 0 1 3 5a2 2 0 0 1 2-2z"/></svg></div><span class="ph">Phone</span></div>
    <div class="field" style="top:199px"><div class="ico"><svg width="12" height="10" viewBox="0 0 12 10" fill="#555"><rect width="12" height="10" rx="1"/><path d="M0 1l6 4 6-4" stroke="#f7f7f7" fill="none"/></svg></div><span class="ph">Email</span></div>
    <div class="field" style="top:253px;height:70px"><div class="ico" style="align-items:flex-start;padding-top:14px"><svg width="13" height="11" viewBox="0 0 13 11" fill="#555"><ellipse cx="5" cy="4" rx="5" ry="3.5"/><ellipse cx="8.5" cy="7" rx="4.5" ry="3"/></svg></div><span class="ph">Message</span></div>
    <div class="submit">Submit Now</div>
  </form>
  <div class="hero-caption">You know your family. We know <em>Senior Living.</em></div>
</section>

<h2 class="section-title" style="top:778px">The Support You Need To Make The Right Choice</h2>
<p class="lead" style="top:828px">Lorem ipsum dolor sit amet, consectetuer adipiscing elit, sed diam nonummy nibh euismod tincidunt ut laoreet dolore magna aliquam erat volutpat. Ut wisi enim ad minim veniam, quis nostrud exerci tation ullamcorper suscipit.</p>

<div class="feature" style="left:142px">
  <svg width="50" height="58" viewBox="0 0 50 58" fill="none" stroke="#8cc63f" stroke-width="2"><circle cx="25" cy="13" r="9"/><path d="M8 56V38a10 10 0 0 1 10-10h14a10 10 0 0 1 10 10v18z"/><path d="M25 28v22M21 28l4 6 4-6"/></svg>
  <p>Dedicated local<br>advisor</p>
</div>
<div class="feature" style="left:328px">
  <svg width="52" height="58" viewBox="0 0 52 58" fill="none" stroke="#8cc63f" stroke-width="2"><path d="M3 28L26 4l23 24"/><path d="M9 22v34h34V22"/><rect x="20" y="38" width="12" height="18"/><rect x="21" y="20" width="10" height="9"/></svg>
  <p>Hand-picked list of communities to match your needs</p>
</div>
<div class="feature" style="left:514px">
  <svg width="52" height="58" viewBox="0 0 52 58" fill="none" stroke="#8cc63f" stroke-width="2"><circle cx="28" cy="24" r="10"/><path d="M28 18v12M25 21h5M25 27h5M28 2v6M20 4l2 5M36 4l-2 5"/><path d="M2 44h10l10 4h10a3 3 0 0 1 0 6H20"/><path d="M32 50l14-8a3 3 0 0 1 3 5L32 56H12"/></svg>
  <p>Full details and<br>pricing</p>
</div>
<div class="feature" style="left:700px">
  <svg width="52" height="58" viewBox="0 0 52 58" fill="none" stroke="#8cc63f" stroke-width="2"><rect x="2" y="8" width="48" height="46"/><path d="M2 18h48M14 2v10M38 2v10M10 26h32v20H10zM18 26v20M26 26v20M34 26v20M10 33h32M10 40h32"/></svg>
  <p>Help scheduling<br>tours</p>
</div>
<div class="feature" style="left:886px">
  <svg width="62" height="52" viewBox="0 0 62 52" fill="none" stroke="#8cc63f" stroke-width="2"><path d="M8 6h32v32H8M40 16h10l10 12v10H40"/><circle cx="18" cy="42" r="5"/><circle cx="48" cy="42" r="5"/><path d="M2 14h14M4 22h12M2 30h10"/></svg>
  <p>Move in<br>support</p>
</div>

<div class="nocost"><b>There's</b> No Cost To You.</div>
<p class="nocost-text">We work with over 20,000 senior living communities.<br>Our community partners pay us for placement services.</p>
<div class="nocost-call">Call (123) 456-7890</div>

<section class="advisor">
  <div class="advisor-people" role="img" aria-label="Row of portrait photos of local advisors, tinted blue"></div>
  <h2>Your local advisor informs. You decide.</h2>
  <p class="sub">Lorem ipsum dolor sit amet, consectetuer adipiscing elit, sed diam nonummy nibh euismod tincidunt ut laoreet.</p>
  <div class="perk" style="left:240px"><div class="ring"><svg width="30" height="58" viewBox="0 0 30 58" fill="none" stroke="#fff" stroke-width="2"><circle cx="15" cy="14" r="12"/><path d="M15 26v30"/></svg></div><p>Insider's tips for the area<br>near you</p></div>
  <div class="perk" style="left:500px"><div class="ring"><svg width="54" height="48" viewBox="0 0 54 48" fill="none" stroke="#fff" stroke-width="2.2"><path d="M27 46L6 25A12 12 0 0 1 27 8a12 12 0 0 1 21 17z"/></svg></div><p>Advice tailored to your<br>unique situation</p></div>
  <div class="perk" style="left:760px"><div class="ring"><svg width="52" height="44" viewBox="0 0 52 44" fill="none" stroke="#fff" stroke-width="2"><circle cx="5" cy="6" r="4"/><circle cx="5" cy="22" r="4"/><circle cx="5" cy="38" r="4"/><path d="M16 6h34M16 22h34M16 38h34"/></svg></div><p>Time saving know-how and<br>resources</p></div>
  <div class="search"><span class="ph">Enter city or postal code</span><div class="go">Find an advisor near you</div></div>
</section>

<h2 class="section-title" style="top:1805px">93% Of Our Customers Recommend Our Service</h2>

<blockquote class="quote" style="left:142px">Lorem ipsum dolor sit amet, consectetuer adipiscing elit, sed diam nonummy nibh euismod tincidunt ut laoreet dolore magna aliquam erat volutpat. Ut wisi enim ad minim veniam, quis nostrud.<span class="mark">”</span></blockquote>
<blockquote class="quote" style="left:457px">Lorem ipsum dolor sit amet, consectetuer adipiscing elit, sed diam nonummy nibh euismod tincidunt ut laoreet dolore magna aliquam erat volutpat. Ut wisi enim ad minim veniam, quis nostrud.<span class="mark">”</span></blockquote>
<blockquote class="quote" style="left:773px">Lorem ipsum dolor sit amet, consectetuer adipiscing elit, sed diam nonummy nibh euismod tincidunt ut laoreet dolore magna aliquam erat volutpat. Ut wisi enim ad minim veniam, quis nostrud.<span class="mark">”</span></blockquote>
<div class="author" style="left:151px"><div class="avatar" role="img" aria-label="Portrait of customer"></div><span>Mara Fenwick</span></div>
<div class="author" style="left:468px"><div class="avatar" role="img" aria-label="Portrait of customer"></div><span>Theo Brandt</span></div>
<div class="author" style="left:784px"><div class="avatar" role="img" aria-label="Portrait of customer"></div><span>Lena Corwin</span></div>
<div class="btn-green" style="top:2092px;left:496px;width:207px;height:38px;line-height:38px">See More Testimonials</div>

<section class="veteran" role="img" aria-label="Waving national flag background, darkened">
  <h2>Access Up To $2,000 Per Month In Veteran's Aid</h2>
  <p>We work with Veterans every day. Most veteran families do not know of a key benefit available to them and their families.<br>It's called the Veteran's Aid and Attendance benefit. This benefit can help pay for senior living and home care.</p>
  <div class="btn-green" style="top:177px;left:536px;width:128px;height:37px;line-height:37px">Learn More</div>
</section>

<h2 class="section-title" style="top:2580px">Senior Assisted Living by State</h2>
<div class="states">
  <ul style="left:159px"><li>Alabama</li><li>Arizona</li><li>Arkansas</li><li>California</li><li>Colorado</li><li>Connecticut</li><li>Delaware</li></ul>
  <ul style="left:301px"><li>District of Columbia</li><li>Florida</li><li>Georgia</li><li>Hawaii</li><li>Idaho</li><li>Illinois</li><li>Indiana</li></ul>
  <ul style="left:486px"><li>Iowa</li><li>Kansas</li><li>Kentucky</li><li>Louisiana</li><li>Maine</li><li>Maryland</li><li>Massachusetts</li></ul>
  <ul style="left:644px"><li>Michigan</li><li>Minnesota</li><li>Mississippi</li><li>Missouri</li><li>Montana</li><li>Nebraska</li><li>Nevada</li></ul>
  <ul style="left:780px"><li>New Hampshire</li><li>New Jersey</li><li>New Mexico</li><li>New York</li><li>North Carolina</li><li>North Dakota</li><li>Ohio</li></ul>
  <ul style="left:950px"><li>Oklahoma</li><li>Oregon</li><li>Pennsylvania</li><li>Rhode Island</li><li>South Carolina</li><li>South Dakota</li><li>Tennessee</li></ul>
</div>

<footer class="site-footer">
  <ul class="foot-nav">
    <li>ASSISTED LIVING</li><li>MEMORY CARE</li><li>NURSING HOMES</li><li>MORE LIVING OPTIONS ⌄</li><li>PLANNING &amp; ADVICE</li><li>HOW OUR SERVICE WORKS</li>
  </ul>
  <div class="foot-rule"></div>
  <p class="copyright">Copyright 2019 The Elder Nook. All Rights Reserved.</p>
  <div class="social"><i></i><i></i><i></i><i></i></div>
</footer>

</body>
</html>
```